Brightwave Reach - Business Card

We need a business card for a Social Media Marketing company that specializes in online marketing for small businesses in Canada using common Social Media platforms such as Pixlora, Chatterly, Blinkpost & Quibber.

I have uploaded a copy of our logo which I would like utilized in the business card. We would like the business card to be modern yet classy design.

Our website is www.brightwavereach.ca

Industry/Entity Type

Marketing

Contact Information for Business Card

Email: info@brightwavereach.ca
Website: www.brightwavereach.ca
Telephone: 604-555-0193

Colors

Designer to choose colors to be used in the design.

Requirements
Must have
• Social Media icons on reverse
• Please add some designs with color.

```html
<!DOCTYPE html>
<html lang="en">
<head>
<meta charset="utf-8">
<title>Brightwave Reach – Business Card</title>
<link rel="stylesheet" href="https://fonts.googleapis.com/css2?family=Open+Sans:wght@400;600;700&family=Oswald:wght@600&display=swap">
<style>
  :root {
    --backdrop: #4a403b;
    --card: #141414;
    --card-edge: #1d1d1d;
    --ink: #f2f2f2;
    --ink-soft: #cfcfcf;
    --mark-grey: #9a9a9a;
    --rule: #bdbdbd;
  }
  * { box-sizing: border-box; margin: 0; padding: 0; }
  html, body { width: 1200px; height: 864px; overflow: hidden; }
  body {
    background: var(--backdrop);
    font-family: "Open Sans", Arial, sans-serif;
    position: relative;
  }
  .card {
    position: absolute;
    width: 560px;
    height: 320px;
    background: linear-gradient(160deg, var(--card-edge), var(--card));
    border-radius: 4px;
    box-shadow: 0 18px 40px rgba(0,0,0,.45);
    color: var(--ink);
  }
  /* reverse side */
  .card--back { left: 50px; top: 70px; }
  .back-brand {
    position: absolute;
    left: 0; right: 0; top: 92px;
    text-align: center;
    font-family: "Oswald", "Arial Narrow", sans-serif;
    font-weight: 600;
    font-size: 34px;
    letter-spacing: 2px;
    text-transform: uppercase;
    color: var(--mark-grey);
  }
  .social-row {
    position: absolute;
    left: 40px; right: 40px; top: 218px;
    display: flex;
    align-items: center;
    gap: 14px;
  }
  .social-row .rule { flex: 1; height: 1px; background: var(--rule); }
  .social-item {
    display: flex; align-items: center; gap: 6px;
    font-size: 12px; color: var(--ink-soft);
  }
  .social-item .dot {
    width: 14px; height: 14px; border-radius: 50%;
    border: 1.5px solid var(--ink-soft);
  }
  /* front side */
  .card--front { left: 590px; top: 470px; }
  .front-brand {
    position: absolute;
    left: 34px; top: 118px;
    width: 220px;
    display: flex; align-items: center; gap: 10px;
  }
  .front-brand .square {
    width: 22px; height: 22px;
    border: 2px solid var(--ink);
    flex: none;
  }
  .front-brand .name {
    font-family: "Oswald", "Arial Narrow", sans-serif;
    font-weight: 600;
    font-size: 30px;
    line-height: 1.05;
    text-transform: uppercase;
    color: var(--ink);
  }
  .divider {
    position: absolute;
    left: 282px; top: 70px;
    width: 2px; height: 180px;
    background: linear-gradient(to bottom, transparent, #e6e6e6 30%, #e6e6e6 70%, transparent);
  }
  .contact { position: absolute; left: 310px; top: 100px; }
  .contact .person { font-weight: 700; font-size: 18px; letter-spacing: .5px; text-transform: uppercase; }
  .contact .role { font-size: 15px; color: var(--ink-soft); margin-bottom: 16px; }
  .contact ul { list-style: none; }
  .contact li {
    display: flex; align-items: center; gap: 8px;
    font-size: 15px; line-height: 24px;
  }
  .contact svg { width: 13px; height: 13px; fill: var(--ink); flex: none; }
</style>
</head>
<body>
  <section class="card card--back" aria-label="Card reverse">
    <div class="back-brand">Brightwave Reach</div>
    <div class="social-row">
      <span class="rule"></span>
      <span class="social-item"><span class="dot"></span>Chatterly</span>
      <span class="social-item"><span class="dot"></span>Pixlora</span>
      <span class="social-item"><span class="dot"></span>Quibber</span>
      <span class="rule"></span>
    </div>
  </section>

  <section class="card card--front" aria-label="Card front">
    <div class="front-brand">
      <span class="square"></span>
      <span class="name">Brightwave Reach</span>
    </div>
    <span class="divider"></span>
    <div class="contact">
      <p class="person">Daniel Reyes</p>
      <p class="role">CEO/FOUNDER</p>
      <ul>
        <li>
          <svg viewBox="0 0 16 16" aria-hidden="true"><path d="M3.5 1.5l2.5 0 1 3.5-1.8 1.2a9 9 0 0 0 4.6 4.6L11 9l3.5 1v2.5c0 1-1 2-2 2C6.5 14.5 1.5 9.5 1.5 3.5c0-1 1-2 2-2z"/></svg>
          604-555-0193
        </li>
        <li>
          <svg viewBox="0 0 16 16" aria-hidden="true"><path d="M1 3h14v10H1z M1.5 3.5L8 9l6.5-5.5" fill="none" stroke="#f2f2f2" stroke-width="1.6"/></svg>
          info@brightwavereach.ca
        </li>
        <li>
          <svg viewBox="0 0 16 16" aria-hidden="true"><circle cx="8" cy="8" r="6.5" fill="none" stroke="#f2f2f2" stroke-width="1.6"/><path d="M1.5 8h13M8 1.5c-3 3.5-3 9.5 0 13M8 1.5c3 3.5 3 9.5 0 13" fill="none" stroke="#f2f2f2" stroke-width="1.2"/></svg>
          www.brightwavereach.ca
        </li>
      </ul>
    </div>
  </section>
</body>
</html>
```